July 2022 Industrial Manufacturer Product Expo Mexico City

We manufacture large screws and fastners for large Mining equipment, Trains, large ships, airplanes, wind turbines, and so on. We also do custom work base on the customer needs. No matter the size we can make it.
We have a Expo coming up with companies all over the world. We have to stand out we are a family own business so our customer service will be above and beyond anyone can provide. We do not have a sales force to push our products and services we provide one on one service.
Plus@!! I'm looking for anything that you designers can come up with if it was your company to put on a business card, plus i want to do a 1 or 2 sided pamphlet, and then a website. We make Speciality Bolts for large mining equipment these bolts can be 3 to 4 foot long!!! Plus fasteners, Nuts, washers, any, size, strengths, special materials, we offer more of a ono on one customer service, We are a small company, family own, but can fulfill any type of orders. We can also provide special time lines for emergency orders. "We keep the machines running we here at KRV don't believe in down time" We want to hear any slogan based on our company to stand out.
Thanks i really appreciate all your work and options that we have to pick on. Plus just a thought we could possibly want to entertain a experience Marketing internet help maybe a employment possibility. Thanks

I need 2 cards one in Spanish and English Like the steel back ground maybe send me in some bright red and blue writing Same with the Black cards Please remove the word Military The logo KRV maybe integrate a picture of a Bolt 🔩 Thank you

Still looking for I need 2 cards one in Spanish and English Like the steel back ground maybe send me in some bright red and blue writing Same with the Black cards try bright writing Please remove the word Military The logo KRV maybe integrate a picture of a Bolt 🔩 Plus will need the company to make a brochure and website next Thank you

Target Market(s)

Large Mining, Ship, Train, Green Energy, VELM, and Government equipment. Throughout the World

Industry/Entity Type

We can Custom Manufacture any type of Fastners for Mining equipment, Trains, Ships, Green energy, Governments, or military projects. wind turbines,

Contact Information for Business Card

I attached the name and contact info that's on a card, plus the Company Logo. Would like industrial looking background with Bright Colors that will stand out!! If we can insert somewhere maybe on back that we "Custom Manufacture Any Size or Quantity Fastners for Large Mining Equipment, Trains, Ships, Green Energy Equipment or Government Projects

Font styles to use
Other font styles liked:
• You Pick, has to be bold, colorful standout, Professional looking Beable to read it.

Colors

Designer to choose colors to be used in the design.

Requirements
Must have
• Need in Spanish and English TO STANDOUT FROM THE REST OF THE EXPO!! See Business card details, Rounded corners
Nice to have
• Can i see some of the darker cards with Bright Red and Blue letters I like to see the different type of card material, heavy thickness, plastic, transparent, Metal types, Bright Colors, I saw like Raised letters like on the logo.

```html
<!DOCTYPE html>
<html lang="es">
<head>
<meta charset="utf-8">
<title>KRV Business Card</title>
<link href="https://fonts.googleapis.com/css2?family=Open+Sans:wght@400;600;700&display=swap" rel="stylesheet">
<style>
  :root {
    --steel-dark: #2b2d31;
    --steel-mid: #54575d;
    --steel-light: #7a7d83;
    --card-white: #ffffff;
    --brand-grey: #4a4b50;
    --tagline-blue: #0a8fd8;
    --navy: #062a86;
    --sky: #0098da;
    --on-blue: #ffffff;
    --faint-mark: rgba(255, 255, 255, 0.10);
  }
  * { margin: 0; padding: 0; box-sizing: border-box; }
  html, body {
    width: 1200px;
    height: 1015px;
    overflow: hidden;
    font-family: "Open Sans", Arial, sans-serif;
  }
  body {
    background: linear-gradient(160deg, var(--steel-dark) 0%, var(--steel-mid) 45%, var(--steel-light) 60%, var(--steel-mid) 75%, var(--steel-dark) 100%);
  }
  .canvas { position: relative; width: 1200px; height: 1015px; }

  .card {
    position: absolute;
    width: 720px;
    height: 412px;
    border-radius: 10px;
    overflow: hidden;
    box-shadow: 0 16px 34px rgba(0, 0, 0, 0.45);
  }

  /* Front */
  .card-front {
    left: 170px;
    top: 60px;
    background: var(--card-white);
    display: flex;
    flex-direction: column;
    align-items: center;
    justify-content: center;
  }
  .brand {
    display: flex;
    align-items: center;
    gap: 22px;
  }
  .brand-dot {
    width: 34px;
    height: 34px;
    border-radius: 50%;
    background: var(--tagline-blue);
  }
  .brand-name {
    font-weight: 700;
    font-size: 112px;
    letter-spacing: 10px;
    line-height: 1;
    color: var(--brand-grey);
  }
  .tagline {
    margin-top: 34px;
    text-align: center;
    color: var(--tagline-blue);
    font-size: 19px;
    line-height: 1.28;
    font-weight: 400;
  }

  /* Back */
  .card-back {
    left: 310px;
    top: 545px;
    background: linear-gradient(150deg, var(--navy) 0%, #0457b0 45%, var(--sky) 100%);
    color: var(--on-blue);
  }
  .faint-mark {
    position: absolute;
    right: 40px;
    top: 50%;
    transform: translateY(-50%) rotate(90deg);
    font-weight: 700;
    font-size: 120px;
    letter-spacing: 10px;
    color: var(--faint-mark);
  }
  .contact {
    position: absolute;
    left: 60px;
    bottom: 62px;
  }
  .person-name {
    font-weight: 700;
    font-size: 28px;
    margin-bottom: 26px;
  }
  .quote-line { font-size: 18px; line-height: 1.3; }
  .phones { margin-top: 22px; font-size: 18px; line-height: 1.4; }
  .phone-row { display: flex; align-items: center; gap: 10px; }
  .phone-row svg { width: 16px; height: 16px; flex: none; }
</style>
</head>
<body>
<main class="canvas">
  <section class="card card-front" aria-label="Frente de la tarjeta">
    <div class="brand">
      <span class="brand-dot" aria-hidden="true"></span>
      <span class="brand-name">KRV</span>
    </div>
    <p class="tagline">
      Custom Manufacture Any Size or Quantity Fastners for Large<br>
      Mining Equipment, Trains, Ships, Green Energy Equipment<br>
      or Government Projects
    </p>
  </section>

  <section class="card card-back" aria-label="Reverso de la tarjeta">
    <div class="faint-mark" aria-hidden="true">KRV</div>
    <div class="contact">
      <p class="person-name">Lic.Marisol Andrea Vega Ruiz</p>
      <p class="quote-line">Cotizaciones en</p>
      <p class="quote-line">ventas.krv@tornillosmail.com</p>
      <div class="phones">
        <p class="phone-row">
          <svg viewBox="0 0 16 16" aria-hidden="true"><path d="M3.5 1.5l2.5 3-1.6 1.6c.8 1.9 2.1 3.2 4 4l1.6-1.6 3 2.5-1.5 2.5C6.8 13.2 2.8 9.2 1 4z" fill="none" stroke="#fff" stroke-width="1.6" stroke-linejoin="round"/></svg>
          5550142873
        </p>
        <p class="phone-row">
          <svg viewBox="0 0 16 16" aria-hidden="true"><rect x="4" y="1" width="8" height="14" rx="1.5" fill="none" stroke="#fff" stroke-width="1.6"/><line x1="7" y1="12.5" x2="9" y2="12.5" stroke="#fff" stroke-width="1.4"/></svg>
          5550198314
        </p>
      </div>
    </div>
  </section>
</main>
</body>
</html>
```